RW Framewell Inc Business cards

We need business cards using our existing logo but slightly modified. Right now the logo says RW Loadbearing Masonry. We want to keep the RW part of the design, but replace the Structural Concrete portion with "FRAMEWELL". Please see the attached file.
Ideally this would be a blank template so we can add Different Names, titles, and phone numbers later.
On the one side we want only the logo and on the other side the detail. I'm attaching an example for you to see.
Please reach out with any other questions. Our address and other details will be given out once we find a design we like.

Target Market(s)

Construction Industry

```html
<!DOCTYPE html>
<html lang="en">
<head>
<meta charset="utf-8">
<title>RW Framewell Inc – Business Cards</title>
<link rel="stylesheet" href="https://fonts.googleapis.com/css2?family=Montserrat:wght@500;600;700&family=Roboto:wght@400;500&display=swap">
<style>
  :root {
    --backdrop: #5a80bd;
    --brand-blue: #2c5fa3;
    --card-white: #f4f4f4;
    --ink-grey: #5d5d5d;
    --edge-grey: #7b7b7b;
    --faint-mark: #e6e6e6;
    --white: #ffffff;
  }
  * { box-sizing: border-box; margin: 0; padding: 0; }
  html, body {
    width: 1200px; height: 852px; overflow: hidden;
    background: var(--backdrop);
  }
  .canvas {
    position: relative; width: 1200px; height: 852px;
  }
  .card {
    position: absolute; top: 276px;
    width: 520px; height: 300px;
    border-radius: 24px; overflow: hidden;
  }
  .card--front { left: 50px; background: var(--brand-blue); }
  .card--back { left: 630px; background: var(--card-white); }

  .wordmark {
    font-family: "Montserrat", sans-serif;
    font-weight: 700;
    line-height: 1;
  }
  .wordmark__initials { display: block; letter-spacing: 2px; }
  .wordmark__name { display: block; letter-spacing: 6px; }

  .card--front .wordmark {
    position: absolute; left: 0; right: 0; top: 92px;
    text-align: center; color: var(--white);
  }
  .card--front .wordmark__initials { font-size: 74px; }
  .card--front .wordmark__name { font-size: 22px; margin-top: 10px; }

  .card--back .wordmark {
    position: absolute; left: 36px; top: 34px;
    color: var(--brand-blue);
  }
  .card--back .wordmark__initials { font-size: 58px; }
  .card--back .wordmark__name { font-size: 17px; margin-top: 8px; letter-spacing: 5px; }

  .faint-mark {
    position: absolute; right: 70px; top: 20px;
    width: 170px; height: 170px; border-radius: 50%;
    background: var(--faint-mark);
  }

  .contact {
    position: absolute; left: 300px; top: 104px;
    font-family: "Roboto", sans-serif; font-size: 11.5px;
    color: var(--ink-grey); line-height: 1.55;
    list-style: none;
  }
  .contact li { display: flex; align-items: flex-start; gap: 7px; }
  .contact svg { width: 11px; height: 11px; margin-top: 3px; flex: none; fill: var(--brand-blue); }
  .contact .no-icon { padding-left: 18px; }

  .person {
    position: absolute; left: 36px; bottom: 52px;
  }
  .person__name {
    font-family: "Montserrat", sans-serif; font-weight: 700;
    font-size: 19px; color: var(--brand-blue);
  }
  .person__title {
    font-family: "Roboto", sans-serif; font-size: 12.5px;
    color: var(--ink-grey); margin-top: 3px;
  }

  .edge-band {
    position: absolute; left: 0; bottom: 0;
    width: 100%; height: 12px; background: var(--edge-grey);
  }
  .web-tab {
    position: absolute; right: 0; bottom: 0;
    width: 250px; height: 40px;
    background: var(--brand-blue);
    border-top-left-radius: 16px;
    display: flex; align-items: center; justify-content: center;
    font-family: "Roboto", sans-serif; font-weight: 500;
    font-size: 12.5px; color: var(--white);
  }
</style>
</head>
<body>
<main class="canvas">
  <section class="card card--front" aria-label="Card front">
    <div class="wordmark">
      <span class="wordmark__initials">RW</span>
      <span class="wordmark__name">FRAMEWELL</span>
    </div>
  </section>

  <section class="card card--back" aria-label="Card back">
    <div class="faint-mark" aria-hidden="true"></div>
    <div class="wordmark">
      <span class="wordmark__initials">RW</span>
      <span class="wordmark__name">FRAMEWELL</span>
    </div>

    <ul class="contact">
      <li>
        <svg viewBox="0 0 24 24" aria-hidden="true"><path d="M6.6 10.8a15.1 15.1 0 0 0 6.6 6.6l2.2-2.2a1 1 0 0 1 1-.25 11.4 11.4 0 0 0 3.6.57 1 1 0 0 1 1 1V20a1 1 0 0 1-1 1A17 17 0 0 1 3 4a1 1 0 0 1 1-1h3.5a1 1 0 0 1 1 1c0 1.25.2 2.45.57 3.57a1 1 0 0 1-.25 1z"/></svg>
        <span>555-010-2233</span>
      </li>
      <li>
        <svg viewBox="0 0 24 24" aria-hidden="true"><path d="M2 5h20v14H2zm2 2v.5l8 5 8-5V7l-8 5z"/></svg>
        <span>dana@framewell-example.com</span>
      </li>
      <li class="no-icon">48 Girder Lane, Millbrook,</li>
      <li class="no-icon">Oregon, US 970010</li>
    </ul>

    <div class="person">
      <p class="person__name">Dana Miller</p>
      <p class="person__title">Managing Director</p>
    </div>

    <div class="edge-band" aria-hidden="true"></div>
    <div class="web-tab">www.framewell-example.com</div>
  </section>
</main>
</body>
</html>
```